Business Card Design Project

I require a business card with the following information on them for various different people;
name
m:
f:
e:
I have a logo already and will attached that. We are in the construction industry. I require something clean and simple but eye catching at the same time. You can use another colour with our logo if you like and you can style the logo as well if you wish. I am open.
Also it needs to be front and back design.
Industry/Entity Type
Construction
Requirements
Must have
- Logo, name, mobile, fax and email address.
Front and back design

```html
<!DOCTYPE html>
<html lang="en">
<head>
<meta charset="utf-8">
<title>Vantorel Developments – Business Cards</title>
<link rel="stylesheet" href="https://fonts.googleapis.com/css2?family=Arimo:wght@400;700&display=swap">
<style>
  :root {
    --page-bg: #2a2a2a;
    --card-bg: #0b0b0b;
    --card-edge: #1c1c1c;
    --brand-green: #7ac143;
    --deep-green: #1f4a12;
    --text-light: #ffffff;
    --rule-grey: #555555;
    --silver-light: #e6e6e6;
    --silver-dark: #3a3a3a;
  }
  * { box-sizing: border-box; margin: 0; padding: 0; }
  html, body { width: 1200px; height: 900px; overflow: hidden; }
  body {
    background: var(--page-bg);
    font-family: "Arimo", Arial, sans-serif;
    position: relative;
  }
  .card {
    position: absolute;
    left: 250px;
    width: 700px;
    height: 400px;
    border-radius: 24px;
    overflow: hidden;
    background: radial-gradient(ellipse at 50% 20%, #1e1e1e 0%, var(--card-bg) 70%);
    border: 1px solid var(--card-edge);
  }
  .card--front { top: 40px; }
  .card--back { top: 465px; }
  .card__bands { position: absolute; inset: 0; width: 100%; height: 100%; }

  .brand {
    position: absolute;
    left: 0; right: 0;
    display: flex;
    justify-content: center;
    align-items: center;
    gap: 12px;
    color: var(--brand-green);
    font-weight: 400;
    letter-spacing: 1px;
    white-space: nowrap;
  }
  .brand__square { width: 22px; height: 22px; background: var(--brand-green); flex: none; }
  .card--front .brand { top: 50px; font-size: 38px; }
  .card--back .brand { top: 140px; font-size: 46px; }
  .card--back .brand__square { width: 26px; height: 26px; }

  .holder {
    position: absolute;
    left: 70px;
    top: 182px;
    width: 480px;
  }
  .holder__name {
    color: var(--brand-green);
    font-size: 26px;
    font-weight: 400;
    letter-spacing: 1px;
    padding-bottom: 10px;
    border-bottom: 1px solid var(--rule-grey);
  }
  .contact {
    margin-top: 8px;
    font-size: 15px;
    line-height: 22px;
    color: var(--text-light);
    white-space: nowrap;
  }
  .contact__row { display: flex; gap: 50px; }
  .contact__label { color: var(--brand-green); }
</style>
</head>
<body>

<section class="card card--front" aria-label="Business card front">
  <svg class="card__bands" viewBox="0 0 700 400" aria-hidden="true">
    <defs>
      <linearGradient id="frontDeep" x1="0" x2="1" y1="0" y2="0">
        <stop offset="0" stop-color="#2d6b18"/>
        <stop offset="0.6" stop-color="#14300c"/>
        <stop offset="1" stop-color="#0b0b0b"/>
      </linearGradient>
      <linearGradient id="frontSilver" x1="0" x2="1">
        <stop offset="0" stop-color="#555"/>
        <stop offset="0.5" stop-color="#d8d8d8"/>
        <stop offset="1" stop-color="#888"/>
      </linearGradient>
    </defs>
    <polygon points="0,338 700,282 700,330 0,385" fill="url(#frontDeep)"/>
    <polygon points="170,350 700,296 700,307 200,358" fill="var(--brand-green)"/>
    <polygon points="440,282 700,258 700,268 455,288" fill="url(#frontSilver)"/>
  </svg>

  <div class="brand"><span class="brand__square"></span>Vantorel Developments</div>

  <div class="holder">
    <h1 class="holder__name">MARK FENTON</h1>
    <div class="contact">
      <div class="contact__row">
        <span><span class="contact__label">Mobile :</span> xxxxxxxxxx</span>
        <span><span class="contact__label">Fax :</span> xxx xxx xxxx</span>
      </div>
      <div><span class="contact__label">E-mail :</span> name@vantorel.example</div>
    </div>
  </div>
</section>

<section class="card card--back" aria-label="Business card back">
  <svg class="card__bands" viewBox="0 0 700 400" aria-hidden="true">
    <defs>
      <linearGradient id="backSilver" x1="0" x2="1">
        <stop offset="0" stop-color="var(--silver-dark)"/>
        <stop offset="0.55" stop-color="var(--silver-light)"/>
        <stop offset="1" stop-color="#5a5a5a"/>
      </linearGradient>
    </defs>
    <rect x="0" y="300" width="700" height="3" fill="var(--brand-green)"/>
    <rect x="0" y="305" width="700" height="42" fill="url(#backSilver)"/>
  </svg>

  <div class="brand"><span class="brand__square"></span>Vantorel Developments</div>
</section>

</body>
</html>
```